Business Card Design

Brambleford Hearth is the name of my health coaching business. My tag line is "Where good health meets real life." I will be working with clients one-on-one and in groups. My target clients are women "of a certain age" who want to be more comfortable in their own skin. We will work together in a 6-month program. The coaching sessions will take place in my kitchen. I will also be conducting monthly cooking classes and field trips - to farmer's markets, speciality markets etc.. for my clients.
Updates

the business name is Brambleford Hearth - I'm not sure how the p got in there at the end of the name

Thank you

Please include the website - www.bramblefordhearth-example.com and the tag line:

Where good health meets real life on the business card.

Thank you

Please add the phone number to the business card - sorry, I forgot to state that in the original brief

(555) 217-4860

Target Market(s)

Women "of a certain age" who want to be more comfortable in their own skin

Industry/Entity Type

Cooking

Contact Information for Business Card

Brambleford Hearth
Where good health meets real life

Tessa Marlowe
Health Coach
(555) 217-4860

Font styles to use
Serif
Sans Serif

Requirements
Must have
• front & back design
I typical like soft colors - and have tended toward greens over time - I'm open although I would not like bright reds, yellows etc..

```html
<!DOCTYPE html>
<html lang="en">
<head>
<meta charset="utf-8">
<title>Brambleford Hearth – Business Card</title>
<link rel="stylesheet" href="https://fonts.googleapis.com/css2?family=Michroma&family=Quicksand:wght@500;600&family=Saira+Condensed:wght@600&display=swap">
<style>
  :root {
    --bg: #d9d9d9;
    --card: #ffffff;
    --green: #1ea35a;
    --ink: #2b2b2b;
    --bar: #3a3a3a;
  }
  * { margin: 0; padding: 0; box-sizing: border-box; }
  html, body { width: 1200px; height: 947px; overflow: hidden; }
  body {
    background: var(--bg);
    font-family: "Quicksand", sans-serif;
    color: var(--ink);
    position: relative;
  }
  .card {
    position: absolute;
    left: 250px;
    width: 700px;
    height: 400px;
    background: var(--card);
    border-radius: 26px;
    box-shadow: 0 6px 18px rgba(0,0,0,.15);
  }
  .card--back { top: 50px; }
  .card--front { top: 497px; }

  .brand {
    font-family: "Michroma", sans-serif;
    font-variant: small-caps;
    font-weight: 400;
    color: var(--green);
    font-size: 24px;
    letter-spacing: 2px;
    text-align: center;
    white-space: nowrap;
  }
  .card--back .brand {
    position: absolute; left: 0; right: 0; top: 172px;
  }
  .tagline {
    position: absolute; left: 0; right: 0; top: 214px;
    text-align: center;
    font-size: 15px;
    color: var(--ink);
  }
  .socials {
    position: absolute; right: 34px; bottom: 30px;
    display: flex; gap: 18px;
  }
  .social {
    display: flex; align-items: center; gap: 6px;
    font-size: 13px; color: var(--ink);
  }
  .social__box {
    width: 18px; height: 18px; background: var(--green); border-radius: 2px;
  }

  .card--front .brand {
    position: absolute; left: 0; right: 0; top: 44px;
  }
  .details {
    position: absolute; left: 150px; top: 118px;
    display: flex; flex-direction: column; gap: 30px;
  }
  .detail {
    display: flex; align-items: center; gap: 16px;
  }
  .detail__icon { width: 44px; height: 44px; flex: none; }
  .detail__bar {
    width: 4px; height: 58px; background: var(--bar); flex: none;
  }
  .detail__text { font-size: 19px; line-height: 1.3; white-space: nowrap; }
  .person__name {
    font-family: "Saira Condensed", sans-serif;
    font-weight: 600;
    font-size: 34px;
    color: var(--green);
    letter-spacing: 1px;
    line-height: 1;
    text-transform: uppercase;
  }
  .person__role { font-size: 17px; margin-top: 4px; }
  .detail--contact .detail__text { font-size: 17px; }
</style>
</head>
<body>

<section class="card card--back" aria-label="Card back">
  <h2 class="brand">Brambleford Hearth</h2>
  <p class="tagline">Where good health meets real life</p>
  <div class="socials">
    <span class="social"><span class="social__box"></span>Cookline</span>
    <span class="social"><span class="social__box"></span>Chirpa</span>
  </div>
</section>

<section class="card card--front" aria-label="Card front">
  <h1 class="brand">Brambleford Hearth</h1>
  <div class="details">
    <div class="detail detail--person">
      <svg class="detail__icon" viewBox="0 0 44 44" aria-hidden="true">
        <circle cx="20" cy="13" r="9" fill="var(--green)"/>
        <path d="M4 40 C4 28 12 24 20 24 C28 24 36 28 36 40 Z" fill="var(--green)"/>
      </svg>
      <span class="detail__bar"></span>
      <div class="detail__text">
        <div class="person__name">Tessa Marlowe</div>
        <div class="person__role">Health Coach</div>
      </div>
    </div>
    <div class="detail detail--address">
      <svg class="detail__icon" viewBox="0 0 44 44" aria-hidden="true">
        <path d="M22 42 C12 28 8 22 8 16 A14 14 0 0 1 36 16 C36 22 32 28 22 42 Z" fill="var(--green)"/>
        <circle cx="22" cy="16" r="5.5" fill="#fff"/>
      </svg>
      <span class="detail__bar"></span>
      <div class="detail__text">
        027 4th floor Hall<br>Ashcombe Road BRF
      </div>
    </div>
    <div class="detail detail--contact">
      <svg class="detail__icon" viewBox="0 0 44 44" aria-hidden="true">
        <circle cx="22" cy="22" r="19" fill="var(--green)"/>
        <g fill="none" stroke="#fff" stroke-width="2">
          <ellipse cx="22" cy="22" rx="8" ry="19"/>
          <line x1="22" y1="3" x2="22" y2="41"/>
          <line x1="3" y1="22" x2="41" y2="22"/>
          <line x1="6" y1="13" x2="38" y2="13"/>
          <line x1="6" y1="31" x2="38" y2="31"/>
        </g>
      </svg>
      <span class="detail__bar"></span>
      <div class="detail__text">
        (555) 217-4860<br>tessa@example.com<br>www.bramblefordhearth-example.com
      </div>
    </div>
  </div>
</section>

</body>
</html>
```